RW Holloway LLC Business Card - Civil Engineering & Consulting Firm

We need a Business Card that is elegant, and masculine.  It is our Professional Civil Engineering & Consulting Company located in San Antonio TX (Not s construction or builder firm- no gears & no tool images please). We provide civil engineering services including  commercial site plans, grading and drainage plans, utility plans, hydraulics and hydrology, land planning, utility coordination, and other general civil engineering services related to commercial and residential development.
We have 2 existing Logos. We would like to convey reliability, strength, trustworthiness and attention to detail.  Blues and orange tones as per logo We are OK with the use of a darker blue in the mix.  We have 2 logo versions - Full Company Name Logo to go on the back of card, & Small Icon Logo for the front w/ personal Info.

Target Market(s)
Architects, Real Estate Developers, Other Strctural Engineers, Surveyers, General Contractors
Industry/Entity Type
Professional Civil Engineering
Contact Information for Business Card
Name, Position, Address, Cell & Office #, email, and company website
Font styles to use
Other font styles liked:
- Avian
Requirements
Should not have
- No Tools, No Gears, no Cranes, or Construction Equipment.

```html
<!DOCTYPE html>
<html lang="en">
<head>
<meta charset="utf-8">
<title>RW Holloway LLC – Business Card</title>
<link href="https://fonts.googleapis.com/css2?family=Montserrat:wght@300;400;500;700&display=swap" rel="stylesheet">
<style>
  :root {
    --backdrop: #3b3b3b;
    --card: #1a1a1b;
    --edge: #6fa4d8;
    --blue: #6fa8e0;
    --orange: #f0962a;
    --white: #f2f2f2;
  }
  * { margin: 0; padding: 0; box-sizing: border-box; }
  html, body {
    width: 1200px; height: 801px; overflow: hidden;
    background: var(--backdrop);
    font-family: "Montserrat", Arial, sans-serif;
  }
  .stage {
    width: 1200px; height: 801px;
    display: flex; align-items: center; justify-content: center; gap: 40px;
  }
  .card {
    position: relative;
    width: 540px; height: 309px;
    background: var(--card);
    border-bottom: 2px solid var(--edge);
    border-left: 2px solid var(--edge);
    box-shadow: 0 14px 30px rgba(0,0,0,.45);
  }

  /* Front */
  .brand { position: absolute; left: 34px; top: 62px; width: 270px; }
  .brand-name {
    display: flex; align-items: center; gap: 9px;
    color: var(--blue); font-weight: 300; font-size: 21px; letter-spacing: 2px;
    white-space: nowrap;
  }
  .brand-mark { width: 12px; height: 12px; background: var(--blue); flex: none; }
  .brand-tagline {
    margin-top: 7px; padding-top: 6px; border-top: 1px solid var(--blue);
    color: var(--orange); font-size: 8.5px; letter-spacing: 3.6px; font-weight: 400;
    white-space: nowrap;
  }
  .holder { position: absolute; right: 34px; top: 66px; text-align: right; }
  .holder-name { color: var(--blue); font-weight: 700; font-size: 17px; letter-spacing: .5px; white-space: nowrap; }
  .holder-title { color: var(--white); font-size: 12px; margin-top: 3px; }
  .divider {
    position: absolute; left: 34px; right: 34px; top: 150px;
    height: 1px; background: var(--edge);
  }
  .address {
    position: absolute; right: 34px; top: 162px; text-align: right;
    color: var(--white); font-size: 12px; line-height: 1.55;
  }
  .contacts {
    position: absolute; left: 34px; bottom: 30px; list-style: none;
    color: var(--white); font-size: 12.5px; line-height: 1.75;
  }
  .contacts li { display: flex; align-items: center; gap: 8px; white-space: nowrap; }
  .contacts svg { width: 11px; height: 11px; flex: none; }

  /* Back */
  .back { display: flex; align-items: center; justify-content: center; }
  .back-name {
    display: flex; align-items: center; gap: 14px;
    color: var(--blue); font-weight: 300; font-size: 30px; letter-spacing: 4px;
    white-space: nowrap;
  }
  .back-mark { width: 18px; height: 18px; background: var(--blue); }
</style>
</head>
<body>
<main class="stage">
  <section class="card front" aria-label="Card front">
    <div class="brand">
      <div class="brand-name"><span class="brand-mark"></span>RW HOLLOWAY LLC</div>
      <div class="brand-tagline">CONSULTING ENGINEERS</div>
    </div>

    <div class="holder">
      <div class="holder-name">DANIEL REYES</div>
      <div class="holder-title">President</div>
    </div>

    <div class="divider"></div>

    <div class="address">
      1870 Harbor View Road<br>Bayside CA 90412
    </div>

    <ul class="contacts">
      <li>
        <svg viewBox="0 0 12 12" aria-hidden="true"><rect x="3" y="0.8" width="6" height="10.4" rx="1" fill="none" stroke="#f0962a" stroke-width="1.4"/></svg>
        555-310-4827
      </li>
      <li>
        <svg viewBox="0 0 12 12" aria-hidden="true"><path d="M2.5 1.5l2 0 1 2.5-1.3 1a6 6 0 0 0 2.8 2.8l1-1.3 2.5 1v2c0 .6-.5 1-1 1A9 9 0 0 1 1.5 2.5c0-.5.4-1 1-1z" fill="#f0962a"/></svg>
        555-310-4828
      </li>
      <li>
        <svg viewBox="0 0 12 12" aria-hidden="true"><rect x="0.8" y="2.5" width="10.4" height="7" fill="#f0962a"/><path d="M1 3l5 3.6L11 3" fill="none" stroke="#1a1a1b" stroke-width="1"/></svg>
        info@rwhollowayconsulting.com
      </li>
      <li>
        <svg viewBox="0 0 12 12" aria-hidden="true"><circle cx="6" cy="6" r="5.2" fill="#f0962a"/><path d="M1 6h10M6 .8c2 2.8 2 7.6 0 10.4M6 .8c-2 2.8-2 7.6 0 10.4" fill="none" stroke="#1a1a1b" stroke-width=".8"/></svg>
        www.rwhollowayconsulting.com
      </li>
    </ul>
  </section>

  <section class="card back" aria-label="Card back">
    <div class="back-name"><span class="back-mark"></span>RW HOLLOWAY LLC</div>
  </section>
</main>
</body>
</html>
```